Computer consultant business card

Bexil Software is a newly started computer consulting company. It's a small one-man company that provides mostly Vornix applications but also websites in collaboration with designers. I'm running this company on the side of full time university studies.

I want the final design to be clean and memorable. Be creative! :)

Some inspiration:
http://www.pixelmarta.com/design/48317
http://www.pixelmarta.com/design/2739164/business-card-design-by-frostlynk
http://www.pixelmarta.com/design/604281/business-card-design-by-koralind-vestrabanu

See attachment for my company logo.
Updates

I would like to thank everyone for submitting! I'll need a couple of days to review and ultimately select a design.

Target Market(s)

Non-technical entrepreneurs and small companies.

Industry/Entity Type

University

Requirements
Must have
• My company logo.
In any way, both colors from my logo.
First- and last name, e-mail and phone number.
Double-sided design.
Nice to have
• Something creative with the symbol in my logo

```html
<!DOCTYPE html>
<html lang="en">
<head>
<meta charset="UTF-8">
<title>Bexil Software — Business Card</title>
<link rel="stylesheet" href="https://fonts.googleapis.com/css2?family=Open+Sans:wght@400;600;700&display=swap">
<style>
  :root {
    --backdrop: #e4e4e4;
    --brand-blue: #3f68ad;
    --brand-blue-deep: #325a9b;
    --brand-blue-light: #4a78bf;
    --ink-black: #060708;
    --logo-grey: #9a9a9a;
    --paper: #ffffff;
    --text-dark: #2a2a2a;
    --card-shadow: rgba(0, 0, 0, 0.22);
  }
  * { box-sizing: border-box; margin: 0; padding: 0; }
  html, body {
    width: 1200px;
    height: 1016px;
    overflow: hidden;
    background: var(--backdrop);
    font-family: "Open Sans", Arial, sans-serif;
  }
  .stage {
    width: 1200px;
    height: 1016px;
    display: flex;
    flex-direction: column;
    align-items: center;
    justify-content: center;
    gap: 60px;
  }
  .card {
    position: relative;
    width: 600px;
    height: 343px;
    border-radius: 18px;
    overflow: hidden;
    box-shadow: 0 10px 26px var(--card-shadow);
  }
  /* Front side */
  .card-front {
    background: radial-gradient(circle at 55% 45%, var(--brand-blue-light) 0%, var(--brand-blue) 45%, var(--brand-blue-deep) 100%);
  }
  .card-front .halo {
    position: absolute;
    left: 180px;
    top: 40px;
    width: 260px;
    height: 260px;
    border-radius: 50%;
    background: rgba(255, 255, 255, 0.06);
  }
  .wordmark {
    position: absolute;
    display: flex;
    align-items: center;
    white-space: nowrap;
  }
  .wordmark-dot {
    border-radius: 50%;
    flex: none;
  }
  .wordmark-text {
    font-weight: 600;
    letter-spacing: 1px;
    line-height: 1;
  }
  .card-front .wordmark {
    left: 50%;
    top: 50%;
    gap: 16px;
    transform: translate(-50%, -50%);
  }
  .card-front .wordmark-dot {
    width: 52px;
    height: 52px;
    background: var(--paper);
  }
  .card-front .wordmark-text {
    font-size: 72px;
    color: var(--paper);
  }
  /* Back side */
  .card-back { background: var(--paper); }
  .card-back .sweep {
    position: absolute;
    inset: 0;
  }
  .card-back .wordmark {
    left: 30px;
    top: 128px;
    gap: 12px;
  }
  .card-back .wordmark-dot {
    width: 32px;
    height: 32px;
    background: var(--brand-blue);
  }
  .card-back .wordmark-text {
    font-size: 44px;
    color: var(--logo-grey);
  }
  .identity {
    position: absolute;
    left: 345px;
    top: 62px;
    text-align: right;
    width: 200px;
  }
  .identity .person-name {
    font-size: 22px;
    font-weight: 700;
    color: var(--brand-blue);
    line-height: 1.1;
  }
  .identity .person-role {
    font-size: 16px;
    color: var(--text-dark);
  }
  .contacts {
    position: absolute;
    left: 225px;
    top: 280px;
    display: flex;
    gap: 30px;
    font-size: 15px;
    color: var(--text-dark);
  }
  .contact-item {
    display: flex;
    align-items: center;
    gap: 7px;
  }
  .contact-icon { width: 22px; height: 22px; }
</style>
</head>
<body>
<main class="stage">
  <section class="card card-front" aria-label="Card front">
    <div class="halo"></div>
    <div class="wordmark">
      <span class="wordmark-dot"></span>
      <span class="wordmark-text">bexil</span>
    </div>
  </section>

  <section class="card card-back" aria-label="Card back">
    <svg class="sweep" viewBox="0 0 600 343" width="600" height="343" aria-hidden="true">
      <path d="M0,0 H340 C262,92 196,204 156,343 H0 Z" fill="var(--ink-black)"/>
      <path d="M352,0 H372 C292,94 228,206 190,343 H168 C208,204 274,92 352,0 Z" fill="var(--brand-blue)"/>
    </svg>
    <div class="wordmark">
      <span class="wordmark-dot"></span>
      <span class="wordmark-text">bexil</span>
    </div>
    <div class="identity">
      <p class="person-name">YOUR NAME</p>
      <p class="person-role">Job Title</p>
    </div>
    <div class="contacts">
      <p class="contact-item">
        <svg class="contact-icon" viewBox="0 0 22 22" aria-hidden="true">
          <circle cx="11" cy="11" r="9.5" fill="none" stroke="var(--brand-blue)" stroke-width="2"/>
          <rect x="8" y="5.5" width="6" height="11" rx="1.2" fill="none" stroke="var(--brand-blue)" stroke-width="1.4"/>
        </svg>
        000-000-000
      </p>
      <p class="contact-item">
        <svg class="contact-icon" viewBox="0 0 22 22" aria-hidden="true">
          <circle cx="11" cy="11" r="9.5" fill="none" stroke="var(--brand-blue)" stroke-width="2"/>
          <rect x="5.5" y="7.5" width="11" height="7.5" fill="none" stroke="var(--brand-blue)" stroke-width="1.4"/>
          <path d="M5.5,7.5 L11,12 L16.5,7.5" fill="none" stroke="var(--brand-blue)" stroke-width="1.4"/>
        </svg>
        name@domainname.com
      </p>
    </div>
  </section>
</main>
</body>
</html>
```